BRANDEMEIER & BRANDEMEIER,LLP NEEDS A NEW LETTERHEAD DESIGN

a conservative yet contemporary layout befitting a long established
firm, consistent with the times, some form of logo so it catches ones attention, and is
admirable, but portrays integrity
Updates

I would like to approve #22066987 Please advise how to do this as it’s confusing on the site so I can approve payment for the designer

Target Market(s)

real estate investors and building management people

Industry/Entity Type

Law Firm

Font styles to use
Serif

Colors

Designer to choose colors to be used in the design.

Requirements
Must have
• some form of conservative logo

```html
<!DOCTYPE html>
<html lang="en">
<head>
<meta charset="utf-8">
<title>Brandemeier &amp; Brandemeier, LLP — Letterhead</title>
<link rel="stylesheet" href="https://fonts.googleapis.com/css2?family=Arimo:wght@400;700&family=Libre+Baskerville&family=Open+Sans:wght@400;700&display=swap">
<style>
  :root{
    --backdrop:#dfe1e3;
    --paper:#ffffff;
    --ink-dark:#3b444e;
    --ink-body:#6f7378;
    --ink-light:#8a8e93;
    --band-dark:#3c4651;
    --band-grey:#a9adb2;
    --rule:#c9ccd0;
  }
  *{margin:0;padding:0;box-sizing:border-box}
  html,body{width:1200px;height:784px;overflow:hidden;background:var(--backdrop)}
  .letterhead{
    position:absolute;left:314px;top:22px;width:572px;height:740px;
    background:var(--paper);box-shadow:0 2px 10px rgba(0,0,0,.12);overflow:hidden;
  }
  .edge-bar{position:absolute;background:var(--band-grey)}
  .edge-bar.dark{background:var(--band-dark)}
  .brand{position:absolute;left:46px;top:44px;display:flex;align-items:center;gap:10px}
  .brand-mark{width:14px;height:14px;background:var(--ink-dark)}
  .brand-name{font-family:"Libre Baskerville",serif;font-size:17px;line-height:1.15;color:var(--ink-dark)}
  .contact{
    position:absolute;right:40px;top:40px;padding-left:10px;border-left:1px solid var(--rule);
    font-family:"Open Sans",sans-serif;font-size:8px;line-height:13px;color:var(--ink-light);
  }
  .contact li{list-style:none;display:flex;align-items:flex-start;gap:5px}
  .contact svg{flex:none;margin-top:3px}
  .contact .address{font-weight:700;color:var(--ink-dark)}
  .body-copy{
    position:absolute;left:60px;top:128px;width:420px;
    font-family:Arimo,sans-serif;font-size:10.5px;line-height:15px;color:var(--ink-body);
  }
  .body-copy p{text-indent:12px;margin-bottom:13px}
  .signature{position:absolute;left:60px;top:530px;width:150px;height:46px;background:linear-gradient(90deg,#d4d7da,#eef0f2);border-radius:4px}
</style>
</head>
<body>
  <main class="letterhead">
    <div class="edge-bar" style="left:0;top:0;width:70px;height:4px"></div>
    <div class="edge-bar dark" style="left:76px;top:0;width:40px;height:4px"></div>
    <div class="edge-bar" style="right:0;top:0;width:50px;height:4px"></div>
    <div class="edge-bar dark" style="left:0;bottom:0;width:150px;height:7px"></div>
    <div class="edge-bar dark" style="left:156px;bottom:0;width:240px;height:7px"></div>
    <div class="edge-bar" style="left:402px;bottom:0;width:170px;height:7px"></div>

    <header class="brand">
      <span class="brand-mark"></span>
      <span class="brand-name">BRANDEMEIER &amp;<br>BRANDEMEIER, LLP</span>
    </header>

    <ul class="contact">
      <li class="address"><svg width="7" height="7" viewBox="0 0 10 10"><path d="M5 0a3.5 3.5 0 0 0-3.5 3.5C1.5 6 5 10 5 10s3.5-4 3.5-6.5A3.5 3.5 0 0 0 5 0z" fill="#6f7378"/></svg><span>48 Harbor Street Suite 210<br>Millbrook, New York 10950</span></li>
      <li><svg width="7" height="7" viewBox="0 0 10 10"><rect x="2" y="0" width="6" height="10" rx="1" fill="#8a8e93"/></svg>(555) 410-2087</li>
      <li><svg width="7" height="7" viewBox="0 0 10 10"><rect x="0" y="2" width="10" height="7" fill="#8a8e93"/></svg>(555) 410-3316</li>
      <li><svg width="7" height="7" viewBox="0 0 10 10"><rect x="0" y="2" width="10" height="7" fill="none" stroke="#8a8e93"/><path d="M0 2l5 4 5-4" fill="none" stroke="#8a8e93"/></svg>info@brandemeierlaw.com</li>
      <li><svg width="7" height="7" viewBox="0 0 10 10"><circle cx="5" cy="5" r="5" fill="#a9adb2"/></svg>www.brandemeierlaw.com</li>
    </ul>

    <section class="body-copy">
      <p>Lorem Ipsum is simply dummy text of the printing and typesetting industry. Lorem Ipsum has been the industry's standard dummy text ever since the 1500s, when an unknown printer took a galley of type and scrambled it to make a type specimen book. It has survived not only five centuries, but also the leap into electronic typesetting, remaining essentially unchanged. It was popularised in the 1960s with the release of Typeline sheets containing Lorem Ipsum passages, and more recently with desktop publishing software like Pressmark Studio including versions of Lorem Ipsum.</p>
      <p>It is a long established fact that a reader will be distracted by the readable content of a page when looking at its layout. The point of using Lorem Ipsum is that it has a more-or-less normal distribution of letters, as opposed to using 'Content here, content here', making it look like readable English. Many desktop publishing packages and web page editors now use Lorem Ipsum as their default model text, and a search for 'lorem ipsum' will uncover many web sites still in their infancy. Various versions have evolved over the years, sometimes by accident, sometimes on purpose (injected humour and the like).</p>
      <p>Contrary to popular belief, Lorem Ipsum is not simply random text. It has roots in a piece of classical Latin literature from 45 BC, making it over 2000 years old. Thomas Wexley, a Latin professor at Ashford Hill College in Virginia, looked up one of the more obscure Latin words, consectetur, from a Lorem Ipsum passage, and going through the cites of the word in classical literature, discovered the undoubtable source. Lorem Ipsum comes from sections 1.10.32 and 1.10.33 of "de Finibus Bonorum et Malorum" structures, to generate Lorem Ipsum which looks reasonable. The generated Lorem Ipsum is therefore always free from repetition, injected humour, or non-characteristic words etc.</p>
    </section>

    <div class="signature" role="img" aria-label="Handwritten signature"></div>
  </main>
</body>
</html>
```